Business card design for Brivo Engineering Tandem

We need a new business card design along with all the necessary to place an order. The company is Brivo Engineering Tandem and we recently updated our logo.

```html
<!DOCTYPE html>
<html lang="en">
<head>
<meta charset="utf-8">
<title>Brivo Engineering Tandem – Business Card</title>
<link href="https://fonts.googleapis.com/css2?family=Kanit:wght@400;500;600&display=swap" rel="stylesheet">
<style>
  :root {
    --backdrop: #2e2e2e;
    --card-white: #ffffff;
    --card-black: #1f1f1f;
    --brand-yellow: #e0bd27;
    --brand-grey: #929292;
    --ink: #1d1d1d;
  }
  * { margin: 0; padding: 0; box-sizing: border-box; }
  html, body { width: 1200px; height: 1059px; overflow: hidden; }
  body {
    background: var(--backdrop);
    font-family: "Kanit", sans-serif;
    position: relative;
  }
  .card {
    position: absolute;
    left: 256px;
    width: 688px;
    height: 393px;
    border-radius: 24px;
    overflow: hidden;
  }
  .card-front { top: 100px; background: var(--card-white); }
  .card-back { top: 536px; background: var(--card-black); display: flex; align-items: center; justify-content: center; }

  .feature-area {
    position: absolute;
    right: 0;
    top: 0;
    width: 330px;
    height: 100%;
    background:
      linear-gradient(to right, #ffffff 0%, rgba(255,255,255,0) 45%),
      linear-gradient(165deg, var(--brand-yellow) 0%, #d9c35a 40%, var(--brand-grey) 100%);
  }

  .brand {
    position: absolute;
    left: 28px;
    top: 52px;
    display: flex;
    align-items: center;
    gap: 14px;
  }
  .brand-square { width: 26px; height: 26px; background: var(--brand-yellow); }
  .brand-name {
    font-weight: 500;
    font-size: 38px;
    line-height: 1;
    color: var(--brand-grey);
    letter-spacing: 0.5px;
  }

  .name-bar {
    position: absolute;
    left: 0;
    top: 155px;
    width: 14px;
    height: 52px;
    background: var(--brand-yellow);
  }
  .person-name {
    position: absolute;
    left: 28px;
    top: 146px;
    font-weight: 600;
    font-size: 34px;
    line-height: 1.1;
    color: var(--brand-yellow);
  }
  .person-role {
    position: absolute;
    left: 28px;
    top: 186px;
    font-size: 18px;
    color: var(--ink);
  }
  .address {
    position: absolute;
    left: 28px;
    top: 226px;
    font-size: 18px;
    line-height: 27px;
    color: var(--ink);
  }
  .contacts {
    position: absolute;
    left: 28px;
    top: 292px;
    list-style: none;
  }
  .contacts li {
    display: flex;
    align-items: center;
    gap: 8px;
    height: 27px;
    font-size: 18px;
    color: var(--ink);
  }
  .contacts svg { width: 15px; height: 15px; fill: var(--brand-yellow); flex: none; }

  .back-name {
    font-weight: 500;
    font-size: 40px;
    color: var(--brand-grey);
    letter-spacing: 0.5px;
  }
</style>
</head>
<body>
  <section class="card card-front">
    <div class="feature-area" role="img" aria-label="Large decorative brand graphic in yellow and grey"></div>

    <div class="brand">
      <span class="brand-square"></span>
      <span class="brand-name">Brivo Engineering Tandem</span>
    </div>

    <span class="name-bar"></span>
    <h1 class="person-name">TOMAS REYLAND</h1>
    <p class="person-role">Managing Director</p>

    <p class="address">Brivo Engineering Tandem<br>24b Halden Way, Corby NN17 4RT</p>

    <ul class="contacts">
      <li>
        <svg viewBox="0 0 16 16" aria-hidden="true"><path d="M1 6c0-2 3-3 7-3s7 1 7 3v1h-3V6H4v1H1z"/><rect x="3" y="8" width="10" height="6" rx="1"/></svg>
        01536 482207
      </li>
      <li>
        <svg viewBox="0 0 16 16" aria-hidden="true"><path d="M1 3h14v1L8 9 1 4z"/><path d="M1 6l7 5 7-5v7H1z"/></svg>
        sales@brivoengineering.co.uk
      </li>
      <li>
        <svg viewBox="0 0 16 16" aria-hidden="true"><circle cx="8" cy="8" r="7"/><path d="M8 1v14M1 8h14" stroke="#fff" stroke-width="1.2" fill="none"/></svg>
        www.brivoengineering.co.uk
      </li>
    </ul>
  </section>

  <section class="card card-back">
    <span class="back-name">Brivo Engineering Tandem</span>
  </section>
</body>
</html>
```